Water ATM Card

Need a design for water ATM cards. Size of card is 3.375 x 2.125 inch
On the Front include the Cedar hollow Logo.
Bottom right corner should have Price $100
On the Back
This card is to be used to access water refills at any Cedar Hollow Water Vending Machines.
Please contact (869) 418 2930 or (869) 534 1276 or email clearflowbox@mailvista.example for any assistance or recharging of card.

```html
<!DOCTYPE html>
<html lang="en">
<head>
<meta charset="utf-8">
<title>Cedar Hollow – Water Card</title>
<link rel="stylesheet" href="https://fonts.googleapis.com/css2?family=Montserrat:wght@400;500;700&display=swap">
<style>
  :root {
    --stage: #262626;
    --paper: #ffffff;
    --brand-blue: #2a57a6;
    --band-blue: #2b62a8;
    --brand-green: #36a546;
    --ink: #1d1d1d;
    --back-top: #2f7fbd;
    --back-bottom: #2e3b86;
    --back-mark: rgba(30, 45, 120, 0.55);
    --back-text: #eef1fb;
  }
  * { margin: 0; padding: 0; box-sizing: border-box; }
  html, body { width: 1200px; height: 1059px; overflow: hidden; }
  body {
    background: var(--stage);
    font-family: "Montserrat", sans-serif;
    position: relative;
  }
  .card {
    position: absolute;
    width: 690px;
    height: 394px;
    border-radius: 22px;
    overflow: hidden;
  }
  /* Front */
  .card--front { left: 255px; top: 87px; background: var(--paper); }
  .brand {
    position: absolute;
    left: 40px; top: 196px;
    width: 290px;
    text-align: center;
    white-space: nowrap;
    font-weight: 700;
    font-size: 26px;
    letter-spacing: 0.5px;
    color: var(--brand-blue);
    text-transform: uppercase;
  }
  .divider {
    position: absolute;
    left: 333px; top: 119px;
    width: 1.5px; height: 157px;
    background: var(--brand-blue);
  }
  .holder { position: absolute; left: 346px; top: 118px; }
  .holder__name {
    font-weight: 700; font-size: 21px; letter-spacing: 0.6px;
    color: var(--brand-blue);
  }
  .holder__role {
    font-size: 14px; color: var(--ink); letter-spacing: 0.5px; margin-top: 2px;
  }
  .contacts { position: absolute; left: 346px; top: 186px; list-style: none; }
  .contacts li {
    display: flex; align-items: center; gap: 7px;
    font-size: 14.5px; color: var(--ink);
    height: 24px;
    white-space: nowrap;
  }
  .contacts li:nth-child(2) { margin-top: 4px; }
  .contacts svg { width: 15px; height: 15px; flex: none; fill: var(--brand-blue); }
  .price {
    position: absolute; right: 47px; top: 329px;
    font-weight: 700; font-size: 19px; color: var(--brand-green);
  }
  .band { position: absolute; left: 0; bottom: 0; width: 100%; height: 15px; }
  /* Back */
  .card--back {
    left: 253px; top: 546px;
    background: linear-gradient(170deg, var(--back-top) 0%, #3d5ea4 35%, var(--back-bottom) 100%);
  }
  .back-intro {
    position: absolute; left: 0; right: 0; top: 52px;
    text-align: center; font-size: 14.5px; line-height: 24px; color: var(--back-text);
  }
  .back-mark {
    position: absolute; left: 0; right: 0; top: 200px;
    text-align: center;
    font-weight: 700; font-size: 40px; letter-spacing: 1px;
    color: var(--back-mark);
    text-transform: uppercase;
  }
  .back-note {
    position: absolute; left: 0; right: 0; top: 290px;
    text-align: center; font-size: 14.5px; line-height: 24px; color: var(--back-text);
  }
</style>
</head>
<body>
  <section class="card card--front">
    <div class="brand">Cedar Hollow</div>
    <div class="divider"></div>
    <div class="holder">
      <div class="holder__name">DARA LINWOOD</div>
      <div class="holder__role">OWER</div>
    </div>
    <ul class="contacts">
      <li>
        <svg viewBox="0 0 24 24" aria-hidden="true"><path d="M6.6 10.8a15.1 15.1 0 0 0 6.6 6.6l2.2-2.2a1 1 0 0 1 1-.25 11.4 11.4 0 0 0 3.6.57 1 1 0 0 1 1 1V20a1 1 0 0 1-1 1A17 17 0 0 1 3 4a1 1 0 0 1 1-1h3.5a1 1 0 0 1 1 1c0 1.25.2 2.45.57 3.57a1 1 0 0 1-.25 1z"/></svg>
        (869) 418 2930
      </li>
      <li>
        <svg viewBox="0 0 24 24" aria-hidden="true"><path d="M7 1h10a2 2 0 0 1 2 2v18a2 2 0 0 1-2 2H7a2 2 0 0 1-2-2V3a2 2 0 0 1 2-2zm0 3v14h10V4zm5 15.2a1.2 1.2 0 1 0 0 2.4 1.2 1.2 0 0 0 0-2.4z"/></svg>
        (869) 534 1276
      </li>
      <li>
        <svg viewBox="0 0 24 24" aria-hidden="true"><path d="M2 5h20v2l-10 6L2 7zm0 4.3 10 6 10-6V19H2z"/></svg>
        clearflowbox@mailvista.example
      </li>
      <li>
        <svg viewBox="0 0 24 24" aria-hidden="true"><path d="M12 2a10 10 0 1 0 0 20 10 10 0 0 0 0-20zm6.9 6h-3a15.6 15.6 0 0 0-1.3-3.9A8 8 0 0 1 18.9 8zM12 4.1A13.6 13.6 0 0 1 13.8 8h-3.6A13.6 13.6 0 0 1 12 4.1zM4.3 14a8 8 0 0 1 0-4h3.4a16.5 16.5 0 0 0 0 4zm.8 2h3a15.6 15.6 0 0 0 1.3 3.9A8 8 0 0 1 5.1 16zm3-8h-3a8 8 0 0 1 4.3-3.9A15.6 15.6 0 0 0 8.1 8zM12 19.9A13.6 13.6 0 0 1 10.2 16h3.6a13.6 13.6 0 0 1-1.8 3.9zm2.3-5.9H9.7a14.7 14.7 0 0 1 0-4h4.6a14.7 14.7 0 0 1 0 4zm.3 5.9a15.6 15.6 0 0 0 1.3-3.9h3a8 8 0 0 1-4.3 3.9zm1.7-5.9a16.5 16.5 0 0 0 0-4h3.4a8 8 0 0 1 0 4z"/></svg>
        www.cedarhollowwater.example
      </li>
    </ul>
    <div class="price">Price $100</div>
    <svg class="band" viewBox="0 0 690 15" preserveAspectRatio="none" aria-hidden="true">
      <polygon points="0,0 330,0 342,15 0,15" fill="var(--band-blue)"/>
      <polygon points="340,0 690,0 690,15 352,15" fill="var(--brand-green)"/>
    </svg>
  </section>

  <section class="card card--back">
    <p class="back-intro">This card is to be used to access water refills<br>at any Cedar Hollow Water Vending Machines.</p>
    <div class="back-mark">Cedar Hollow</div>
    <p class="back-note">Please contact (869) 418 2930 or (869) 534 1276<br>or email clearflowbox@mailvista.example<br>for any assistance or recharging of card.</p>
  </section>
</body>
</html>
```